International business needs business cards

Our company, DRV Ventures Inc. is in the business of supplying a range construction products with particular emphasis on CEMENT. We have developed our own brand - TORVAN SUPPLIES - with which to infiltrate the market. We are launching our brand of cement (TORVAN Type IS Cement) into the Caribbean which is unlike anything this market has ever seen. A monopoly has existed here for the past 60-odd years and the market has now opened to allow the importation of other brands and consumers are anxious and ready for change/improvement. We are very excited to be launching and want to make a great first impression. We will be conducting workshops and seminars (from government level to the hardware store owners) and we want our business card to give us the strong, confident introduction that we need.

Target Market(s)

construction; builders; engineers; home owners

Industry/Entity Type

Construction

Contact Information for Business Card

Marisol Depree
CEO
cell # 1 555 4180736
Ground floor,Lindell Plaza Suite 2734
George Town,Grand Cayman
Cayman Islands,KY1-4823
EMAIL: m.depree@drvventuresinc.example
web site drvventuresinc.example

COMPANY: skype info drv.ventures.example

second card
Yvette Brannock-Depree
CFO
CELL# 1 555 607 3941
George Town,Grand Cayman
Cayman Islands,KY1-4823
EMAIL: y.brannockdepree@drvventuresinc.example
website drvventuresinc.example

Requirements
Must have
• Business cards must display BOTH logos - DRV is the company and TORVAN is the brand.

```html
<!DOCTYPE html>
<html lang="en">
<head>
<meta charset="utf-8">
<title>DRV Ventures Inc. — Business Card</title>
<link rel="stylesheet" href="https://fonts.googleapis.com/css2?family=Open+Sans:wght@400;600;700&display=swap">
<style>
  :root {
    --backdrop: #2b2b2d;
    --card: #ffffff;
    --ink: #111111;
    --ink-soft: #333333;
    --accent: #8c1c1c;
    --rule: #222222;
  }
  * { box-sizing: border-box; margin: 0; padding: 0; }
  html, body {
    width: 1200px; height: 900px; overflow: hidden;
    background: var(--backdrop);
    font-family: "Open Sans", Arial, sans-serif;
    color: var(--ink);
  }
  .stage { position: relative; width: 1200px; height: 900px; }
  .card {
    position: absolute;
    width: 680px; height: 390px;
    background: var(--card);
    border-radius: 26px;
    box-shadow: 0 12px 30px rgba(0,0,0,.45);
    overflow: hidden;
  }
  .card--brand { left: 120px; top: 45px; }
  .card--contact { left: 400px; top: 465px; }

  /* Brand side */
  .brand-mark {
    position: absolute; left: 0; right: 0; top: 120px;
    display: flex; justify-content: center; align-items: center; gap: 16px;
  }
  .brand-mark__dot {
    width: 44px; height: 44px; border-radius: 50%;
    background: var(--ink-soft);
  }
  .brand-mark__name {
    font-size: 56px; font-weight: 700; letter-spacing: 6px; color: var(--ink-soft);
  }
  .brand-handle {
    position: absolute; left: 0; right: 0; top: 318px;
    display: flex; justify-content: center; align-items: center; gap: 8px;
    font-size: 17px; font-weight: 600; color: var(--ink);
  }
  .brand-handle__dot {
    width: 13px; height: 13px; border-radius: 50%; background: var(--accent);
  }

  /* Contact side */
  .company {
    position: absolute; left: 44px; top: 112px;
    display: flex; align-items: center; gap: 14px;
  }
  .company__square { width: 74px; height: 74px; background: var(--accent); flex: none; }
  .company__name {
    width: 190px;
    font-size: 28px; font-weight: 700; color: var(--ink); line-height: 1.1;
  }

  .person {
    position: absolute; right: 40px; top: 70px; text-align: right;
  }
  .person__name { font-size: 27px; font-weight: 700; letter-spacing: .5px; }
  .person__role { font-size: 13px; color: var(--accent); margin-top: 1px; }
  .person__rule {
    position: absolute; right: 40px; top: 130px; width: 300px;
    border-top: 1.5px solid var(--rule);
  }
  .address {
    position: absolute; right: 40px; top: 140px; text-align: right;
    font-size: 14px; font-weight: 600; line-height: 1.4; color: var(--ink);
    font-style: normal;
  }
  .contact-rule {
    position: absolute; left: 40px; right: 40px; top: 262px;
    border-top: 1.5px solid var(--rule);
  }
  .contacts {
    position: absolute; left: 44px; top: 274px; list-style: none;
    font-size: 16px; font-weight: 600; line-height: 1.55;
  }
  .contacts li { display: flex; align-items: center; gap: 9px; }
  .contacts svg { width: 13px; height: 13px; flex: none; }
</style>
</head>
<body>
<main class="stage">
  <section class="card card--brand" aria-label="Brand side of business card">
    <div class="brand-mark">
      <span class="brand-mark__dot"></span>
      <span class="brand-mark__name">TORVAN</span>
    </div>
    <p class="brand-handle"><span class="brand-handle__dot"></span>drv.ventures.example</p>
  </section>

  <section class="card card--contact" aria-label="Contact side of business card">
    <div class="company">
      <span class="company__square"></span>
      <span class="company__name">DRV Ventures Inc.</span>
    </div>

    <div class="person">
      <p class="person__name">MARISOL DEPREE</p>
      <p class="person__role">CEO</p>
    </div>
    <div class="person__rule"></div>
    <address class="address">
      Ground floor,Lindell Plaza Suite 2734<br>
      George Town,Grand Cayman<br>
      Cayman Islands,KY1-4823
    </address>

    <div class="contact-rule"></div>
    <ul class="contacts">
      <li>
        <svg viewBox="0 0 16 16" aria-hidden="true"><path fill="#8c1c1c" d="M3 1l3 3-1.5 2a9 9 0 0 0 5.5 5.5L12 10l3 3-2 2C7 15 1 9 1 3z"/></svg>
        1 555 4180736
      </li>
      <li>
        <svg viewBox="0 0 16 16" aria-hidden="true"><rect x="1" y="3" width="14" height="10" fill="none" stroke="#8c1c1c" stroke-width="1.8"/><path d="M1 3l7 6 7-6" fill="none" stroke="#8c1c1c" stroke-width="1.8"/></svg>
        m.depree@drvventuresinc.example
      </li>
      <li>
        <svg viewBox="0 0 16 16" aria-hidden="true"><circle cx="8" cy="8" r="7" fill="#8c1c1c"/><path d="M1 8h14M8 1c-3 3-3 11 0 14M8 1c3 3 3 11 0 14" fill="none" stroke="#fff" stroke-width="1"/></svg>
        www.drvventuresinc.example
      </li>
    </ul>
  </section>
</main>
</body>
</html>
```